Women's Jewellery startup needs a captivating, beautifully designed and intuitive online store

[12/24 update]

Added 2 additional documents:

Feedback on designs received so far: designer feedback.docx
Product images from catalogue: products images.docx

Please read the feedback provided on designs provided so far to guide you further on your submission. The product images can be used to create promotional banners for the site.

@@@Added a document (VELISTO JEWELLERY_checklist.docx) which can be used by designers as a checklist when submitting their designs to ensure all aspects of the requirements have been covered @@@

+++IMPORTANT BUT NOT SPECIFIED IN THE REQUIREMENTS DOCUMENT - DESIGN SHOULD INCLUDE SUPPORT FOR MOBILE FRIENDLY SITE TOO+++

***Previous experience designing Jewellery online stores preferred (not essential)***

The name of the online Jewellery store is "Velisto Jewellery" and the business is based in Hong Kong. It will be run by 2 stay at home mothers. We need a Shopify themed store designed that will achieve the following objectives in order of priority:

• Conversion: The primary objective of the design/content is to prompt the customer to make a purchase. While this may sound obvious, it is mentioned so as not to distract the design process by focusing on other objectives (which are also important). The site also needs to be optimized so as to rank high in search engine searches for relevant keywords (SEO)
• Navigation: An intuitive interface which takes away a lot of the thinking from the customer by making it obvious what they need to do when they visit the store
• Engagement: Encourages the customer to spend time on the website and share content with their social network

Where applicable, the design of the store should reflect as closely as possible the mission statements and words outlined below:

• Jewellery you’ll fall in love with
• We want every client to leave the store with a smile
• We want to be able to provide the best service we can in every situation no matter what
• We aim to increase our business by word of mouth; therefore we tell people things about our store that makes it interesting for them to share
• We love every customer, no matter how difficult things get
• We, as a team, are so well informed about our products and brands that we always have the best information for our customers
• We celebrate women here!
• We celebrate life in here!
• We celebrate beauty here!
• We celebrate families here, as jewellery often stays within families.
• We will always try to make an extra step
• We will always try to exceed the expectation of our customers
• We will go as far as we possibly can to attract a customer back to our store and connect with us
• Every client that leaves our store knows more about jewellery because we passionately told him about it
• Romantic, classic, love, warm, cool, stylish

A draft functional specification is attached with this brief. We would like the design to reflect as closely as possible the functional requirements outlined in the document. Open to suggestions to improve upon the functional requirements.

Target Market(s)

Women aged 18-55

Industry/Entity Type

Jewelry Store

Coding

Coded - Design and coding required

Number of Pages Required

5+ page

Font styles to use
Other font styles liked:
• Myriad Pro as per Logo but open to any font that complements this one

Requirements
Must have
• 1. A look that encourages the user to make a purchase
• 2. An intuitive, easy to navigate and engaging interface
• 3. Primary colour scheme as defined in the functional specification attached
• 4. Simplistic look, not too cluttered
Nice to have
• 1. Closely matching the functional requirements of the site as outlined in the requirements specification but open to any better ideas

```html
<!DOCTYPE html>
<html lang="en">
<head>
<meta charset="utf-8">
<title>Velisto Jewellery – Newsletter Signup</title>
<link href="https://fonts.googleapis.com/css2?family=Open+Sans:wght@300;400;600;700&family=Montserrat:wght@400;600;700&display=swap" rel="stylesheet">
<style>
:root{
  --gold:#c9962e;
  --gold-dark:#8a6a1f;
  --ink:#1d1d1d;
  --muted:#7a7a7a;
  --line:#d9d9d9;
  --paper:#ffffff;
  --header-bg:#f4f4f4;
  --footer-bg:#2a2a2a;
  --shade:rgba(0,0,0,.8);
}
*{margin:0;padding:0;box-sizing:border-box}
html,body{width:1200px;height:2350px;overflow:hidden}
body{position:relative;background:var(--paper);font-family:"Open Sans",Arial,sans-serif;color:var(--ink)}
.abs{position:absolute}

/* top bar & header */
.topbar{left:0;top:0;width:1200px;height:35px;background:var(--gold-dark)}
.topbar-links{right:136px;top:0;height:35px;display:flex;gap:34px;align-items:center;font-size:11px;color:#fff}
.header{left:0;top:35px;width:1200px;height:98px;background:var(--header-bg)}
.brand{left:136px;top:0;width:154px;height:122px;background:var(--paper);display:flex;flex-direction:column;align-items:center;justify-content:center;gap:6px}
.brand-name{font-family:"Montserrat",sans-serif;font-weight:700;font-size:22px;letter-spacing:3px;color:var(--gold)}
.brand-tag{font-size:9px;color:var(--gold-dark)}
.nav{right:136px;top:72px;display:flex;gap:40px;align-items:center;font-family:"Montserrat",sans-serif;font-weight:600;font-size:11px}
.nav .active{background:var(--gold);color:#fff;padding:4px 10px}

/* hero */
.hero{left:0;top:133px;width:1200px;height:530px;background:radial-gradient(ellipse at 62% 40%,#7a5a4c 0%,#3a2a26 30%,#111 65%)}
.hero-title{left:136px;top:300px;font-size:46px;line-height:54px;color:var(--gold)}
.hero-title .light{font-weight:300;display:block}
.hero-title .bold{font-weight:700;display:block}
.hero-dots{left:136px;top:502px;display:flex;gap:14px;align-items:center}
.hero-dots span{width:9px;height:9px;border-radius:50%;background:#bbb}
.hero-dots .on{width:14px;height:14px;border:2px solid #bbb;background:transparent}

/* offers */
.offer{top:699px;width:295px;height:230px;color:#fff;text-align:center;background:linear-gradient(160deg,#4a3420,#1a1410)}
.offer h3{margin-top:26px;font-size:21px;font-weight:700;text-decoration:underline}
.offer .deal{margin-top:12px;font-size:24px;font-weight:300}
.offer .deal b{color:var(--gold);font-weight:700}
.offer .cond{margin-top:8px;font-size:15px}
.offer .big{font-size:28px;font-weight:700;color:var(--gold)}
.offer .until{position:absolute;bottom:18px;left:0;right:0;font-size:14px;border-top:1px solid #fff;margin:0 40px;padding-top:8px}

/* filters */
.filters{left:135px;top:969px;width:115px;font-size:10px;color:var(--muted)}
.filters h4{font-family:"Montserrat",sans-serif;font-size:12px;color:var(--ink);font-weight:700}
.filters h5{font-family:"Montserrat",sans-serif;font-size:11px;color:var(--ink);font-weight:700;padding-bottom:6px;border-bottom:1px solid var(--ink);margin:26px 0 8px}
.filters li{list-style:none;height:19px;display:flex;align-items:center;gap:6px}
.filters li::before{content:"";width:7px;height:7px;border:1px solid #aaa}
.range{position:relative;height:26px;margin-top:16px}
.range .bar{position:absolute;top:6px;left:0;width:115px;height:2px;background:var(--gold)}
.range .knob{position:absolute;top:2px;width:10px;height:10px;border-radius:50%;background:var(--gold)}
.range .lbl{position:absolute;top:16px;font-size:9px}

.sort{right:130px;top:971px;font-size:11px;color:var(--muted)}
.sort b{color:var(--ink)}

/* products */
.card{width:240px;border:1px solid #eee;text-align:center}
.card-img{margin:22px auto 0;width:120px;height:120px;border-radius:8px;background:radial-gradient(circle,#e8c98a,#b88a3a 60%,#f4f4f4 72%)}
.card h6{margin-top:28px;font-family:"Open Sans",sans-serif;font-size:14px;font-weight:700}
.price{margin-top:8px;font-size:19px;font-weight:700;color:var(--gold)}
.price s{font-size:12px;color:var(--muted);font-weight:400}
.card p{margin:12px auto 22px;width:150px;font-size:10px;color:var(--muted);line-height:13px}
.more{left:599px;top:1927px;width:180px;height:40px;background:var(--gold);color:#fff;font-family:"Montserrat",sans-serif;font-weight:600;font-size:13px;display:flex;align-items:center;justify-content:center}

/* footer */
.footer{left:0;top:2032px;width:1200px;height:318px;background:var(--footer-bg);color:#bbb}
.fcol{top:58px;font-size:11px;line-height:17px}
.fcol h6{font-family:"Montserrat",sans-serif;font-size:11px;color:#fff;margin-bottom:16px}
.socials{display:flex;gap:10px}
.socials span{width:24px;height:24px;border-radius:50%;background:#3a5a8a}
.f-input{width:207px;height:41px;background:#fff;color:#999;font-size:11px;padding:12px 14px}
.f-btn{margin-top:18px;width:75px;height:29px;background:var(--gold);color:#fff;font-size:10px;font-weight:700;display:flex;align-items:center;justify-content:center}
.f-rule{left:136px;top:229px;width:936px;height:1px;background:#555}
.copy{left:0;top:271px;width:1200px;text-align:center;font-size:11px}

/* modal */
.shade{left:0;top:0;width:1200px;height:2350px;background:var(--shade)}
.modal{left:287px;top:857px;width:627px;height:406px;background:var(--paper);text-align:center}
.modal h2{margin-top:64px;font-size:24px;font-weight:700;letter-spacing:.3px}
.modal-fields{position:absolute;left:61px;top:154px;display:flex;gap:17px}
.field{width:251px;height:51px;border:2px solid #d0d0d0;font-size:11px;font-weight:600;text-align:left;padding:16px 20px}
.signup{position:absolute;left:243px;top:260px;width:141px;height:55px;background:var(--gold);color:#fff;font-size:19px;font-weight:700;display:flex;align-items:center;justify-content:center}
.close{left:594px;top:13px}
</style>
</head>
<body>

<div class="abs topbar"></div>
<div class="abs topbar-links"><span>Sign In</span><span>Wishlist (0)</span><span>HKD ▾</span><span>MY CART (0)</span>
<svg width="14" height="14" viewBox="0 0 14 14"><circle cx="6" cy="6" r="4.5" fill="none" stroke="#fff" stroke-width="1.6"/><line x1="9.5" y1="9.5" x2="13" y2="13" stroke="#fff" stroke-width="1.6"/></svg></div>
<div class="abs header"></div>
<div class="abs brand"><span class="brand-name">VELISTO</span><span class="brand-tag">jewellery you'll fall in love with</span></div>
<nav class="abs nav"><span class="active">HOME</span><span>PRODUCTS</span><span>OUR STORY</span><span>CONTACT US</span><span>FAQ</span><span>MY ACCOUNT</span></nav>

<div class="abs hero" role="img" aria-label="Portrait of a woman wearing drop diamond earrings against a dark background"></div>
<h1 class="abs hero-title"><span class="light">We celebrate</span><span class="bold">women here!</span></h1>
<div class="abs hero-dots"><span></span><span></span><span class="on"></span><span></span><span></span></div>

<section class="abs offer" style="left:135px" role="img" aria-label="Gold jewellery offer banner"><h3>GOLD</h3><div class="deal">Extra <b>10% off</b></div><div class="cond">for orders over</div><div class="big">$500</div><div class="until">till March 31st, 2018</div></section>
<section class="abs offer" style="left:454px" role="img" aria-label="Diamond rings offer banner"><h3>DIAMOND</h3><div class="deal">Extra <b>10% off</b></div><div class="cond">DIAMOND RINGS</div><div class="until">till March 31st, 2018</div></section>
<section class="abs offer" style="left:774px" role="img" aria-label="Silver jewellery offer banner"><h3>SILVER</h3><div class="deal">Extra <b>15% off</b></div><div class="cond">for orders over</div><div class="big">$200</div><div class="until">till March 31st, 2018</div></section>

<aside class="abs filters">
<h4>FILTER BY</h4>
<h5>TYPE</h5><ul><li>Rings</li><li>Necklaces</li><li>Bracelets</li><li>Earring</li><li>Charms</li></ul>
<h5>COLLECTION</h5><ul><li>Gold</li><li>Silver</li><li>Diamond</li><li>Ruby</li><li>Sapphire</li><li>Emerald</li><li>Moissanite</li></ul>
<h5>METAL</h5><ul><li>10K Rose Gold</li><li>14K Gold Rose</li><li>18K Gold Rose</li><li>10K Yellow Gold</li><li>14K Yellow Rose</li><li>18K Yellow Rose</li><li>Silver</li><li>Gold plated</li><li>Silver plated</li></ul>
<h5>GEMSTONE</h5><ul><li>Amethyst</li><li>Aquamarine</li><li>Sapphire</li><li>Topaz</li><li>Diamond</li><li>Citrine</li><li>Cubic Zirconia</li><li>Emerald</li><li>Garnet</li><li>Moissanite</li><li>Quartz</li><li>Ruby</li><li>Tanzanite</li></ul>
<h5>PRICE RANGE</h5>
<div class="range"><div class="bar"></div><div class="knob" style="left:0"></div><div class="knob" style="left:72px"></div><span class="lbl" style="left:0">$0</span><span class="lbl" style="left:68px">$100</span></div>
</aside>

<div class="abs sort">Price: <b>high to low</b> &nbsp; Price: <b>low to high</b></div>

<article class="abs card" style="left:309px;top:1026px"><div class="card-img" role="img" aria-label="Ring product photo"></div><h6>RING 1</h6><div class="price">$49.99 <s>$29.99</s></div><p>Lorem Ipsum is simply dummy text of the printing and</p></article>
<article class="abs card" style="left:570px;top:1026px"><div class="card-img" role="img" aria-label="Ring product photo"></div><h6>RING 2</h6><div class="price">$59.99 <s>$29.99</s></div><p>Lorem Ipsum is simply dummy text of the printing and</p></article>
<article class="abs card" style="left:831px;top:1026px"><div class="card-img" role="img" aria-label="Gold bracelet product photo"></div><h6>BRACELET</h6><div class="price">$89.99 <s>$29.99</s></div><p>Lorem Ipsum is simply dummy text of the printing and</p></article>

<article class="abs card" style="left:309px;top:1313px"><div class="card-img" role="img" aria-label="Gold cuff bracelet product photo"></div><h6>BRACELET 1</h6><div class="price">$99.99 <s>$29.99</s></div><p>Lorem Ipsum is simply dummy text of the printing and</p></article>
<article class="abs card" style="left:570px;top:1313px"><div class="card-img" role="img" aria-label="Gold drop earrings product photo"></div><h6>EARRINGS</h6><div class="price">$69.99 <s>$29.99</s></div><p>Lorem Ipsum is simply dummy text of the printing and</p></article>
<article class="abs card" style="left:831px;top:1313px"><div class="card-img" role="img" aria-label="Ruby necklace product photo"></div><h6>NECKLACES 1</h6><div class="price">$29.99 <s>$29.99</s></div><p>Lorem Ipsum is simply dummy text of the printing and</p></article>

<article class="abs card" style="left:309px;top:1619px"><div class="card-img" role="img" aria-label="Gemstone necklace product photo"></div><h6>NECKLACES 2</h6><div class="price">$39.99 <s>$29.99</s></div><p>Lorem Ipsum is simply dummy text of the printing and</p></article>
<article class="abs card" style="left:570px;top:1619px"><div class="card-img" role="img" aria-label="Pendant necklace product photo"></div><h6>NECKLACES 3</h6><div class="price">$69.99 <s>$29.99</s></div><p>Lorem Ipsum is simply dummy text of the printing and</p></article>
<article class="abs card" style="left:831px;top:1619px"><div class="card-img" role="img" aria-label="Rose gold ring product photo"></div><h6>NECKLACES 4</h6><div class="price">$39.99 <s>$29.99</s></div><p>Lorem Ipsum is simply dummy text of the printing and</p></article>

<div class="abs more">VIEW MORE ITEMS</div>

<footer class="abs footer">
<div class="abs fcol" style="left:136px"><h6>ABOUT US</h6>Our Story<br>Wholesale Inquiries</div>
<div class="abs fcol" style="left:318px"><h6>SHOPPING</h6>Orders<br>Wishlist<br>Size Guide</div>
<div class="abs fcol" style="left:478px"><h6>CUSTOMER CARE</h6>Returns<br>FAQs<br>Care &amp; Warranty<br>Contact Us</div>
<div class="abs fcol" style="left:674px"><h6>FOLLOW US</h6><div class="socials"><span></span><span></span><span></span></div></div>
<div class="abs fcol" style="left:865px"><h6>NEWSLETTER</h6><div class="f-input">E mail Id</div><div class="f-btn">SIGNUP</div></div>
<div class="abs f-rule"></div>
<div class="abs copy">Copyrights @ 2017 All Rights Reserved</div>
</footer>

<div class="abs shade"></div>

<div class="abs modal" role="dialog" aria-label="Newsletter signup">
<h2>SIGN UP TO THE NEWSLETTER</h2>
<div class="modal-fields"><div class="field">NAME</div><div class="field">E MAIL ID</div></div>
<div class="signup">SIGNUP</div>
<svg class="abs close" width="36" height="36" viewBox="0 0 36 36" aria-label="Close"><circle cx="18" cy="18" r="17" fill="#c9962e"/><circle cx="18" cy="18" r="11" fill="#fff"/><path d="M13.5 13.5l9 9M22.5 13.5l-9 9" stroke="#c9962e" stroke-width="3.2" stroke-linecap="round"/></svg>
</div>

</body>
</html>
```